Property Developer - Simple yet Sophisticated and Sharp Business Card

We are a medium sized property developer involved mainly in townhouse developments and land subdivisions.

The company is looking for a simple, sharp and sophisticated business card that will be given to contractors, land owners, financiers etc and thus will need to look professional.

Property development related graphics and art can be used, however the card is not to be too "busy" or crowded. Our company name is Kestrel Developments which could possibly be incorporated into the graphics or artwork.

Single sided and/or double sided designs will be acceptable.

A Simple, Sophisticated, Sharp design please!

Good Luck !

```html
<!DOCTYPE html>
<html lang="en">
<head>
<meta charset="utf-8">
<title>Kestrel Developments – Business Card</title>
<link href="https://fonts.googleapis.com/css2?family=Barlow:wght@300;400&display=swap" rel="stylesheet">
<style>
  :root {
    --page: #ffffff;
    --card-edge: #9a9a9a;
    --brand-brown: #4a3218;
    --rule: #e8dfd2;
    --text-light: #efe9df;
    --text-muted: #a38f76;
  }
  html, body {
    margin: 0;
    padding: 0;
    width: 1200px;
    height: 900px;
    overflow: hidden;
    background: var(--page);
    font-family: "Barlow", "Helvetica Neue", Arial, sans-serif;
    font-weight: 300;
  }
  .canvas {
    position: relative;
    width: 1200px;
    height: 900px;
  }
  .card {
    position: absolute;
    left: 70px;
    top: 126px;
    width: 1062px;
    height: 648px;
    box-sizing: border-box;
    border: 1px solid var(--card-edge);
    background: var(--page);
  }
  .band {
    position: absolute;
    left: 70px;
    top: 186px;
    width: 1062px;
    height: 528px;
    background: var(--brand-brown);
  }
  .rule {
    position: absolute;
    left: 70px;
    width: 1062px;
    height: 2px;
    background: var(--rule);
  }
  .rule--top { top: 235px; }
  .rule--contact { top: 589px; }

  .company-name {
    position: absolute;
    left: 162px;
    top: 248px;
    margin: 0;
    font-size: 40px;
    line-height: 1;
    font-weight: 300;
    letter-spacing: 0.5px;
    color: var(--text-light);
  }
  .person-name {
    position: absolute;
    left: 162px;
    top: 526px;
    margin: 0;
    font-size: 30px;
    line-height: 1;
    font-weight: 300;
    letter-spacing: 0.5px;
    color: var(--text-light);
  }
  .person-role {
    position: absolute;
    left: 162px;
    top: 558px;
    margin: 0;
    font-size: 13px;
    line-height: 1;
    letter-spacing: 0.5px;
    color: var(--text-muted);
  }
  .contact-block {
    position: absolute;
    top: 602px;
    white-space: nowrap;
  }
  .contact-block--phone { left: 162px; }
  .contact-block--email { left: 388px; }
  .contact-block--postal { left: 804px; }

  .contact-label {
    display: block;
    font-size: 12px;
    line-height: 1;
    letter-spacing: 0.5px;
    color: var(--text-muted);
    margin: 0 0 3px;
  }
  .contact-value {
    display: block;
    margin: 0;
    font-size: 23px;
    line-height: 30px;
    letter-spacing: 0.5px;
    color: var(--text-light);
  }
  .contact-label--fax { margin-top: 4px; }
</style>
</head>
<body>
<div class="canvas">
  <div class="card"></div>
  <div class="band"></div>
  <div class="rule rule--top"></div>
  <div class="rule rule--contact"></div>

  <h1 class="company-name">KESTREL DEVELOPMENTS</h1>

  <p class="person-name">DANIEL MARSH</p>
  <p class="person-role">PROJECT MANAGER</p>

  <div class="contact-block contact-block--phone">
    <span class="contact-label">PHONE</span>
    <span class="contact-value">(07) 3250 6814</span>
    <span class="contact-label contact-label--fax">FAX</span>
    <span class="contact-value">(07) 3250 6815</span>
  </div>

  <div class="contact-block contact-block--email">
    <span class="contact-label">EMAIL</span>
    <span class="contact-value">PROJECTS.KESTRELDEV</span>
    <span class="contact-value">@MAILBOX.COM</span>
  </div>

  <div class="contact-block contact-block--postal">
    <span class="contact-label">POSTAL</span>
    <span class="contact-value">PO BOX 4217</span>
    <span class="contact-value">MARLOW HEIGHTS</span>
    <span class="contact-value">QLD 4127</span>
  </div>
</div>
</body>
</html>
```